We need a business card design for a new company located in Harlow Springs, NV, entitled 'BrightPath Chiropractic & Holistic Center'. Our services include restoration of health and vitality, spinal exam, health assessment, dietary & fitness programs, lymphatic & therapeutic massage, detox & remineralize body wraps, far infrared sauna therapy

Industry/Entity Type

Business

Contact Information for Business Card

BrightPath Chiropractic & Holistic Center, Marlene Okafor LMT, 4215 Elm Ridge Rd., Suite 310, Harlow Springs, NV 77482, 712-555-0193

```html
<!DOCTYPE html>
<html lang="en">
<head>
<meta charset="utf-8">
<title>BrightPath Chiropractic &amp; Holistic Center – Business Card</title>
<link rel="stylesheet" href="https://fonts.googleapis.com/css2?family=Lato:wght@400&family=Gelasio:wght@500;700&family=Arimo:wght@400&display=swap">
<style>
  :root {
    --bg: #e4e1dc;
    --card-white: #ffffff;
    --card-black: #050505;
    --navy: #1d5a85;
    --teal: #16a08c;
    --sky: #1a9ad6;
    --grey-text: #5e5e5e;
    --ink: #111111;
    --light: #f4f4f4;
  }
  * { margin: 0; padding: 0; box-sizing: border-box; }
  html, body { width: 1189px; height: 1200px; overflow: hidden; background: var(--bg); }
  .canvas { position: relative; width: 1189px; height: 1200px; }

  .card { position: absolute; left: 140px; width: 918px; height: 524px; overflow: hidden; }
  .card-front { top: 45px; background: var(--card-white); }
  .card-back { top: 624px; background: var(--card-black); }

  .front-wave { position: absolute; inset: 0; }

  .brand { position: absolute; left: 0; width: 494px; top: 190px; text-align: center; }
  .brand-name { display: inline-flex; align-items: center; gap: 12px;
    font-family: "Gelasio", serif; font-weight: 700; font-size: 50px; color: var(--grey-text); line-height: 1; }
  .brand-dot { width: 18px; height: 18px; border-radius: 50%; background: var(--teal); }
  .brand-tagline { margin-top: 6px; font-family: "Arimo", sans-serif; font-size: 22px; color: var(--grey-text); letter-spacing: 0.5px; }
  .brand-tagline .amp { color: var(--teal); }

  .holder { position: absolute; right: 52px; top: 54px; text-align: right; }
  .holder-name { font-family: "Gelasio", serif; font-weight: 500; font-size: 54px; color: var(--navy); line-height: 1; }
  .holder-title { margin-top: 10px; font-family: "Lato", sans-serif; font-size: 30px; color: var(--ink); }

  .contacts { position: absolute; right: 50px; top: 318px; list-style: none;
    font-family: "Lato", sans-serif; color: var(--light); }
  .contacts li { display: flex; justify-content: flex-end; align-items: center; gap: 22px; height: 43.5px; font-size: 25px; }
  .contacts li.address { font-size: 22px; }
  .icon { width: 21px; height: 21px; background: var(--navy); border-radius: 2px; flex: none; display: block; }

  .services-title { position: absolute; left: 149px; top: 52px;
    font-family: "Lato", sans-serif; font-size: 58px; color: var(--sky); line-height: 1; }
  .services-rule { position: absolute; left: 100px; right: 0; top: 110px; height: 2px; background: var(--teal); }
  .services-dot { position: absolute; left: 40px; top: 80px; width: 56px; height: 56px; border-radius: 50%; background: var(--teal); }
  .service-list { position: absolute; left: 212px; top: 140px; list-style: none;
    font-family: "Lato", sans-serif; font-size: 29px; color: var(--light); }
  .service-list li { display: flex; align-items: center; gap: 36px; height: 49.5px; }
  .service-list li::before { content: ""; width: 18px; height: 18px; border-radius: 50%; background: var(--light); flex: none; }
</style>
</head>
<body>
<main class="canvas">
  <section class="card card-front">
    <svg class="front-wave" width="918" height="524" viewBox="0 0 918 524" aria-hidden="true">
      <defs>
        <linearGradient id="band" x1="0" y1="0" x2="0" y2="1">
          <stop offset="0" stop-color="#16a08c"/>
          <stop offset="1" stop-color="#1d6f8f"/>
        </linearGradient>
      </defs>
      <path d="M0 253 C120 300 250 320 420 280 C560 245 640 200 720 215 C800 228 860 262 918 294 L918 524 L0 524 Z" fill="url(#band)"/>
      <path d="M0 310 C120 340 260 345 420 300 C560 262 650 225 720 228 C800 232 860 265 918 294 L918 524 L0 524 Z" fill="var(--card-black)"/>
    </svg>

    <div class="brand">
      <div class="brand-name"><span class="brand-dot"></span>BrightPath</div>
      <p class="brand-tagline">Chiropractic <span class="amp">&amp;</span> Holistic Center</p>
    </div>

    <div class="holder">
      <h1 class="holder-name">Daniel Reyes</h1>
      <p class="holder-title">President</p>
    </div>

    <ul class="contacts">
      <li>712-555-0193 <span class="icon" aria-label="phone"></span></li>
      <li>www.brightpathcare.com <span class="icon" aria-label="website"></span></li>
      <li>hello@brightpathcare.com <span class="icon" aria-label="email"></span></li>
      <li class="address">Marlene Okafor LMT, 4215 Elm Ridge Rd., Suite 310, Harlow Springs, NV 77482 <span class="icon" aria-label="location"></span></li>
    </ul>
  </section>

  <section class="card card-back">
    <span class="services-dot"></span>
    <h2 class="services-title">services</h2>
    <div class="services-rule"></div>
    <ul class="service-list">
      <li>dietary &amp; fitness programs</li>
      <li>lymphatic &amp; therapeutic massage</li>
      <li>spinal exam</li>
      <li>health assessment</li>
      <li>far infrared sauna therapy</li>
      <li>restoration of health and vitality</li>
      <li>detox &amp; remineralize body wraps</li>
    </ul>
  </section>
</main>
</body>
</html>
```